Bench Advertisement - We Buy Houses Design Needed

Need a catchy, simple but elegant design for bus benches to advertise our company.

We need our website, or phone number, and a smal description (1-2 bulletpoints of what we do and what we offer)

The tricky part is for the designer to fit everything and make the website name as part of the title and fitting everything so that people passing by on the street can see what we offer.

Our website is quickdealhomebuyer.com - (916) 555-0143

Something simple but something that catches the eye of walking pedestrians, and drivers driving by the bench.

Our company buys houses, any condition, any situation, we buy houses for cash and close quickly. You can use this description to create a few bulletpoints however you like. Must follow dimensions in attachment.

Target Market(s)

People in foreclosure, about to lose their homes, people that need a quick cash sale of their property

Industry/Entity Type

Real Estate

Requirements
Must have
• catchy, website name, phone number, few brief bulletpoints about what we offer, colors that will catch peoples eye while walking or driving - advertisement will be placed on bus benches - visit our website to see the type of houses we buy - Also have more work for winner of design with possible bonuses
Nice to have
• Feel free to use description or images on our website - make sure the description is just bullet points and it fits with the overall theme / size of the advertisement - Bold bright colors - put yourself in their shoes (if you were going through financial difficulties and about to lose your house to foreclosure or auction, what would you want to see to pick up the phone and call us for a quick sale of your house?) (or if you have a house that you are having a problem with, problem renters, unkept/beat up house, what would make you want to call us and sell your house to us?)

```html
<!DOCTYPE html>
<html lang="en">
<head>
<meta charset="utf-8">
<title>Quick Deal Home Buyer – Bench Advertisement</title>
<link rel="stylesheet" href="https://fonts.googleapis.com/css2?family=Oswald:wght@300;400&display=swap">
<style>
  :root {
    --page: #e7e7e3;
    --green-dark: #3a6a32;
    --green-mid: #6a9a3a;
    --green-light: #8fbf3e;
    --green-glow: #b8d84a;
    --phone-green: #2f5a26;
    --white: #ffffff;
    --accent: #c7e04a;
  }
  * { margin: 0; padding: 0; box-sizing: border-box; }
  html, body {
    width: 1200px; height: 1061px; overflow: hidden;
    background: var(--page);
    font-family: "Oswald", sans-serif;
  }
  .bench-ad {
    position: absolute; left: 40px; top: 280px;
    width: 1120px; height: 500px;
    background: var(--green-dark);
    box-shadow: 0 12px 30px rgba(0,0,0,.25);
    overflow: hidden;
  }
  .feature-band {
    position: absolute; left: 0; top: 100px;
    width: 100%; height: 290px;
    background: linear-gradient(90deg, var(--green-mid) 0%, var(--green-mid) 45%, #73a23c 100%);
    border-top: 2px solid var(--green-light);
  }
  .hero-photo {
    position: absolute; left: 0; top: 100px;
    width: 500px; height: 330px;
    background:
      radial-gradient(ellipse at 35% 40%, var(--green-glow) 0%, rgba(143,191,62,.7) 35%, rgba(106,154,58,0) 75%),
      linear-gradient(90deg, #5f9a34 0%, #4f8a2e 70%, rgba(106,154,58,0) 100%);
  }
  .brand {
    position: absolute; left: 40px; top: 150px;
    display: flex; align-items: center; gap: 10px;
    color: var(--white); font-weight: 400; font-size: 18px;
    letter-spacing: .5px; text-transform: uppercase;
  }
  .brand-dot {
    width: 16px; height: 16px; border-radius: 50%;
    background: var(--green-dark);
  }
  .photo-caption {
    position: absolute; left: 40px; top: 396px;
    color: var(--white); font-weight: 300; font-size: 19px;
  }
  .offer {
    position: absolute; left: 520px; top: 118px;
    width: 570px; text-align: center;
  }
  .website {
    color: var(--white); font-weight: 400; font-size: 50px;
    line-height: 1.1; letter-spacing: .3px;
  }
  .phone {
    margin-top: 18px;
    display: flex; align-items: center; justify-content: center; gap: 14px;
    color: var(--phone-green); font-weight: 300; font-size: 46px; line-height: 1;
  }
  .phone svg { width: 40px; height: 40px; }
  .benefits { list-style: none; margin-top: 26px; color: var(--white); font-weight: 300; font-size: 27px; line-height: 1.45; }
  .benefits li { display: flex; align-items: center; justify-content: center; gap: 12px; }
  .marker { width: 10px; height: 20px; }
</style>
</head>
<body>
  <main class="bench-ad">
    <section class="feature-band"></section>
    <div class="hero-photo" role="img" aria-label="Photo of two hands exchanging a white house cut-out for a dollar bill on a soft green background"></div>

    <div class="brand"><span class="brand-dot"></span>Quick Deal Home Buyer</div>
    <p class="photo-caption">pick up the phone and call us for a quick sale of your house</p>

    <div class="offer">
      <h1 class="website">quickdealhomebuyer.com</h1>
      <p class="phone">
        <svg viewBox="0 0 40 40" aria-hidden="true">
          <circle cx="20" cy="20" r="17" fill="none" stroke="var(--phone-green)" stroke-width="2.5"/>
          <path d="M14 11c-1.5 1-2.5 2.5-2 4.5 1.3 5.5 5.5 10 11 12 2 .7 3.8-.2 5-1.8l-3.5-3.2-2.3 1.4c-2.6-1.3-4.5-3.5-5.7-6.2l1.6-2.1z" fill="var(--phone-green)"/>
        </svg>
        (916) 555-0143
      </p>
      <ul class="benefits">
        <li>Our company buys houses, Any condition, Any situation</li>
        <li>
          <svg class="marker" viewBox="0 0 10 20" aria-hidden="true"><path d="M0 0l10 10-10 10z" fill="var(--accent)"/></svg>
          We buy houses for cash and close quickly
          <svg class="marker" viewBox="0 0 10 20" aria-hidden="true"><path d="M10 0L0 10l10 10z" fill="var(--accent)"/></svg>
        </li>
      </ul>
    </div>
  </main>
</body>
</html>
```